Business Card Design Project - del varosi group

dear Sirs

we need business card design for our group ( DEL Varosi Group ) , i have got the Logo design of our group from pixel harbor in previous , so all need details relating to our group i think available with you, as well as the the chosen logo design

we hope to provide us with business card logo that to be appropaite and satisfactory to us .

thanks

note : logo design of our group is attached .
Updates

Reason: please extend the deadline of my project for additional 15 days because i didn't received appropriate design for our gruop yet . kindly beaware that i have received 77 design till now , supossed to send me 200-250 design at least . thanks

Target Market(s)

contents

name : Kerem EL Nadiri

position : Operation Manager

Industry/Entity Type

Business

Requirements
Must have

• person name

group logo
Nice to have
• logo color matching with back background

```html
<!DOCTYPE html>
<html lang="en">
<head>
<meta charset="utf-8">
<title>DEL Varosi Group – Business Card</title>
<link href="https://fonts.googleapis.com/css2?family=Open+Sans:wght@400;600;700&display=swap" rel="stylesheet">
<style>
  :root {
    --stage: #e9e6e2;
    --card-white: #ffffff;
    --brand-blue: #1f5d9e;
    --band-blue: #1b6ab8;
    --back-blue-light: #2277c4;
    --back-blue-dark: #0d4f93;
    --text-grey: #5b5f66;
    --rule-grey: #c9ccd1;
    --gold-light: #e6c879;
    --gold-dark: #b98a2c;
  }
  * { box-sizing: border-box; margin: 0; padding: 0; }
  html, body { width: 1200px; height: 758px; overflow: hidden; }
  body {
    background: var(--stage);
    font-family: "Open Sans", Arial, sans-serif;
    position: relative;
  }
  .card {
    position: absolute;
    top: 224px;
    width: 540px;
    height: 310px;
    border-radius: 26px;
    overflow: hidden;
    box-shadow: 0 10px 28px rgba(0,0,0,0.22);
  }
  /* Front */
  .card--front { left: 40px; background: var(--card-white); }
  .front__brand {
    position: absolute;
    left: 34px; top: 92px;
    display: flex; align-items: center; gap: 10px;
  }
  .brand__square { width: 16px; height: 16px; background: var(--brand-blue); }
  .brand__name {
    font-weight: 700; font-size: 21px; color: var(--brand-blue);
    letter-spacing: 0.2px;
  }
  .front__divider {
    position: absolute; left: 296px; top: 36px;
    width: 1px; height: 170px; background: var(--rule-grey);
  }
  .front__person { position: absolute; left: 312px; top: 34px; }
  .person__name { font-weight: 700; font-size: 21px; color: var(--brand-blue); line-height: 1.2; }
  .person__role { font-size: 13px; color: var(--text-grey); margin-top: 2px; }
  .contact-list { list-style: none; margin-top: 16px; }
  .contact-list li {
    display: flex; align-items: center; gap: 7px;
    font-size: 13px; color: var(--text-grey); line-height: 20px;
  }
  .contact-list svg { width: 11px; height: 11px; fill: var(--text-grey); flex: none; }
  .front__band {
    position: absolute; left: 0; right: 0; top: 222px; height: 40px;
    background: var(--band-blue);
  }
  .front__ornament {
    position: absolute; right: 34px; top: 196px;
    width: 78px; height: 56px; border-radius: 40px 40px 40px 8px;
    background: linear-gradient(160deg, var(--gold-light), var(--gold-dark));
    border: 3px solid var(--card-white);
  }
  .front__address {
    position: absolute; left: 0; right: 0; top: 274px;
    text-align: center; font-size: 13px; letter-spacing: 0.6px;
    color: var(--text-grey);
  }
  /* Back */
  .card--back {
    left: 620px;
    background: linear-gradient(135deg, var(--back-blue-light), var(--back-blue-dark));
    color: #ffffff;
  }
  .back__brand {
    position: absolute; left: 0; right: 0; top: 110px;
    display: flex; justify-content: center; align-items: center; gap: 14px;
  }
  .card--back .brand__square { width: 22px; height: 22px; background: #ffffff; }
  .card--back .brand__name { color: #ffffff; font-size: 34px; }
  .back__web {
    position: absolute; left: 0; right: 0; top: 200px;
    text-align: center; font-size: 17px; letter-spacing: 1px; font-weight: 600;
  }
</style>
</head>
<body>

<section class="card card--front" aria-label="Business card front">
  <div class="front__brand">
    <span class="brand__square"></span>
    <span class="brand__name">DEL Varosi Group</span>
  </div>
  <div class="front__divider"></div>
  <div class="front__person">
    <p class="person__name">Kerem EL Nadiri</p>
    <p class="person__role">Operation Manager</p>
    <ul class="contact-list">
      <li><svg viewBox="0 0 10 10"><rect x="2.5" y="0" width="5" height="10" rx="1"/></svg>+2348105550142</li>
      <li><svg viewBox="0 0 10 10"><path d="M2 0l2 2-1 1.5c.7 1.5 2 2.8 3.5 3.5L8 6l2 2-1.5 2C4 9.5.5 6 0 1.5z"/></svg>+2348105550142</li>
      <li><svg viewBox="0 0 10 10"><circle cx="5" cy="3" r="2.5"/><path d="M0 10c0-3 2.2-4.5 5-4.5S10 7 10 10z"/></svg>+2348105550142 varosistays.com</li>
      <li><svg viewBox="0 0 10 10"><rect x="0" y="2" width="10" height="7" rx="1"/></svg>name@website.com</li>
      <li><svg viewBox="0 0 10 10"><circle cx="5" cy="5" r="5"/></svg>www.website.com</li>
    </ul>
  </div>
  <div class="front__band"></div>
  <div class="front__ornament" role="img" aria-label="Gold swoosh ornament"></div>
  <p class="front__address">Street name, City, State, zip code</p>
</section>

<section class="card card--back" aria-label="Business card back">
  <div class="back__brand">
    <span class="brand__square"></span>
    <span class="brand__name">DEL Varosi Group</span>
  </div>
  <p class="back__web">www.website.com</p>
</section>

</body>
</html>
```